Simple Recipe eBook

I need the graphic work done for a simple recipe ebook, I have attached all of the required information for it, as well as our company logo. Further company info can be found at velorabix.com

I would like each recipe page to include 2 recipes, each recipe needs to include ingredients, picture, method, and nutritional info.

I would like the style to appear fresh and healthy, with lots of graphics and colours to match.
Please let me know if you need any guidance

Target Market(s)

Females aged from 15-25

Industry/Entity Type

It Company

```html
<!DOCTYPE html>
<html lang="en">
<head>
<meta charset="utf-8">
<title>Chinese five spice beef with rice</title>
<link rel="stylesheet" href="https://fonts.googleapis.com/css2?family=Pacifico&family=Bellota+Text:ital,wght@0,400;0,700;1,700&display=swap">
<style>
  :root {
    --plum: #483a4d;
    --plum-light: #7a6480;
    --paper: #f4f3f6;
    --white: #ffffff;
    --ink: #1d1a1e;
    --tan: #c4a595;
    --cocoa: #9c7068;
    --mint: #8fc6a8;
    --butter: #e9c97b;
    --shadow: #d9d8dc;
    --card-shadow: #3a2f3e;
  }
  * { margin: 0; padding: 0; box-sizing: border-box; }
  html, body { width: 1200px; height: 1000px; overflow: hidden; background: var(--white); }
  body { position: relative; font-family: "Bellota Text", "Trebuchet MS", sans-serif; color: var(--ink); }
  .page { position: absolute; left: 250px; top: 26px; width: 708px; height: 942px; overflow: hidden; background: var(--paper); }
  .hero { position: absolute; left: 0; top: 0; width: 708px; height: 288px; background: var(--plum); }
  .pattern-band { position: absolute; left: 0; width: 708px; height: 42px; background: var(--plum-light); opacity: .75; }
  .pattern-band.top { top: 0; }
  .pattern-band.bottom { bottom: 0; opacity: .55; }
  .header-arc { position: absolute; left: 0; top: 0; }
  .section-label { position: absolute; left: 0; top: 12px; width: 708px; text-align: center; font-family: "Pacifico", cursive; font-size: 30px; color: var(--ink); }
  .recipe-title { position: absolute; left: 42px; top: 108px; width: 280px; font-family: "Pacifico", cursive; font-size: 25px; line-height: 33px; color: var(--white); }
  .recipe-intro { position: absolute; left: 42px; top: 196px; width: 300px; font-size: 12px; line-height: 16px; color: var(--white); }
  .facts-shadow { position: absolute; left: 375px; top: 120px; width: 306px; height: 140px; background: var(--card-shadow); }
  .facts { position: absolute; left: 367px; top: 112px; width: 306px; height: 139px; background: var(--white); }
  .fact { position: absolute; top: 21px; width: 53px; text-align: center; }
  .fact-icon { display: block; width: 53px; height: 44px; }
  .fact-value { display: block; height: 36px; line-height: 38px; font-size: 23px; }
  .fact-label { display: block; height: 23px; line-height: 23px; font-size: 10px; font-weight: 700; }
  .fact-label.dark { color: var(--white); }
  .columns-head { position: absolute; top: 300px; font-family: "Pacifico", cursive; font-size: 26px; }
  .ingredients-shadow { position: absolute; left: 0; top: 354px; }
  .ingredient-list { position: absolute; left: 44px; top: 361px; width: 200px; list-style: none; font-size: 11px; font-weight: 700; font-style: italic; line-height: 15.6px; }
  .ingredient-list li { position: relative; padding-left: 14px; }
  .ingredient-list li::before { content: "+"; position: absolute; left: 0; top: 0; font-style: normal; font-weight: 700; }
  .step-tag { position: absolute; left: 303px; width: 62px; height: 28px; }
  .step-text { position: absolute; left: 378px; width: 304px; font-size: 11px; line-height: 15.2px; }
  .plate-area { position: absolute; left: 0; top: 634px; width: 708px; height: 308px; background: var(--plum); }
  .plate-photo { position: absolute; left: 0; top: 0; }
</style>
</head>
<body>
<main class="page">
  <header class="hero">
    <div class="pattern-band top" role="img" aria-label="Row of soft circle pattern"></div>
    <svg class="header-arc" width="708" height="90" viewBox="0 0 708 90" aria-hidden="true">
      <path d="M168 0 Q354 150 540 0 Z" fill="var(--white)"/>
    </svg>
    <div class="section-label">Dinner</div>
    <h1 class="recipe-title">Chinese five spice beef with rice</h1>
    <p class="recipe-intro">Save time and feel better with this healthy meal made for busy nights.</p>

    <div class="facts-shadow"></div>
    <div class="facts">
      <div class="fact" style="left:12px">
        <span class="fact-icon" style="background:var(--tan)" role="img" aria-label="Knife and board icon"></span>
        <span class="fact-value">0:05</span>
        <span class="fact-label" style="background:var(--tan)">To Prep</span>
      </div>
      <div class="fact" style="left:69px">
        <span class="fact-icon" style="background:var(--cocoa)" role="img" aria-label="Cooking pot icon"></span>
        <span class="fact-value">0:10</span>
        <span class="fact-label" style="background:var(--cocoa)">To Cook</span>
      </div>
      <div class="fact" style="left:126px">
        <span class="fact-icon" style="background:var(--mint)" role="img" aria-label="Vegetables icon"></span>
        <span class="fact-value">8</span>
        <span class="fact-label" style="background:var(--mint)">Ingreds.</span>
      </div>
      <div class="fact" style="left:183px">
        <svg class="fact-icon" viewBox="0 0 53 44" role="img" aria-label="Difficulty scale icon">
          <rect width="53" height="44" fill="var(--plum)"/>
          <text x="8" y="26" font-size="10" fill="var(--white)" font-family="Bellota Text, sans-serif">1</text>
          <text x="23" y="13" font-size="10" fill="var(--white)" font-family="Bellota Text, sans-serif">2</text>
          <text x="40" y="26" font-size="10" fill="var(--white)" font-family="Bellota Text, sans-serif">3</text>
          <circle cx="26.5" cy="32" r="8" fill="none" stroke="var(--white)" stroke-width="2"/>
          <circle cx="26.5" cy="32" r="5" fill="var(--white)"/>
        </svg>
        <span class="fact-value">Easy</span>
        <span class="fact-label dark" style="background:var(--plum)">Difficulty</span>
      </div>
      <div class="fact" style="left:240px">
        <svg class="fact-icon" viewBox="0 0 53 44" role="img" aria-label="Servings icon">
          <rect width="53" height="44" fill="var(--butter)"/>
          <circle cx="20" cy="17" r="6" fill="var(--white)"/>
          <circle cx="34" cy="17" r="6" fill="var(--white)"/>
          <path d="M9 44 v-8 q0-10 11-10 q11 0 11 10 v8 Z" fill="var(--white)"/>
          <path d="M23 44 v-8 q0-10 11-10 q11 0 11 10 v8 Z" fill="var(--white)"/>
        </svg>
        <span class="fact-value">4</span>
        <span class="fact-label" style="background:var(--butter)">Servings</span>
      </div>
    </div>
  </header>

  <section class="ingredients">
    <h2 class="columns-head" style="left:42px">Ingredients</h2>
    <svg class="ingredients-shadow" width="290" height="270" viewBox="0 0 290 270" aria-hidden="true">
      <polygon points="0,8 280,8 230,270 0,270" fill="var(--shadow)"/>
      <polygon points="0,0 273,0 220,260 0,260" fill="var(--butter)"/>
    </svg>
    <ul class="ingredient-list">
      <li>1 1/2 tablespoons salt-reduced soy sauce</li>
      <li>2 teaspoons Chinese five spice powder</li>
      <li>500g beef rump steak, trimmed</li>
      <li>2 teaspoons peanut oil</li>
      <li>6 green onions, cut into 5cm lengths</li>
      <li>2 bunches choy sum, leaves and stems separated, roughly chopped</li>
      <li>2 tablespoons oyster sauce</li>
      <li>Steamed GoldenGrain Jasmine</li>
      <li>Fragrant Rice, to serve</li>
    </ul>
  </section>

  <section class="method">
    <h2 class="columns-head" style="left:303px">Method</h2>

    <svg class="step-tag" style="top:349px" viewBox="0 0 62 28" aria-hidden="true">
      <polygon points="5,4 62,4 58,28 1,28" fill="var(--shadow)"/>
      <polygon points="0,0 60,0 56,24 0,24" fill="var(--tan)"/>
      <text x="6" y="17" font-size="13" font-weight="700" font-style="italic" font-family="Bellota Text, sans-serif" fill="var(--ink)">Step 1</text>
    </svg>
    <p class="step-text" style="top:347px">Combine soy sauce and five spice in a shallow bowl. Add steak. Turn to coat. Heat half the oil in a frying pan over high heat. Cook steak for 2 to 3 minutes each side for medium or until cooked to your liking. Transfer to a plate. Rest, loosely covered with foil, for 5 minutes.</p>

    <svg class="step-tag" style="top:463px" viewBox="0 0 62 28" aria-hidden="true">
      <polygon points="5,4 62,4 58,28 1,28" fill="var(--shadow)"/>
      <polygon points="0,0 60,0 56,24 0,24" fill="var(--cocoa)"/>
      <text x="6" y="17" font-size="13" font-weight="700" font-style="italic" font-family="Bellota Text, sans-serif" fill="var(--ink)">Step 2</text>
    </svg>
    <p class="step-text" style="top:464px">Meanwhile, heat a wok over medium-high heat. Add remaining oil. Swirl to coat. Add onion and choy sum stems. Stir-fry for 2 minutes or until onion has softened. Add choy sum leaves, oyster sauce and 2 tablespoons cold water. Stir-fry for 2 to 3 minutes or until leaves have wilted.</p>

    <svg class="step-tag" style="top:572px" viewBox="0 0 62 28" aria-hidden="true">
      <polygon points="5,4 62,4 58,28 1,28" fill="var(--shadow)"/>
      <polygon points="0,0 60,0 56,24 0,24" fill="var(--mint)"/>
      <text x="6" y="17" font-size="13" font-weight="700" font-style="italic" font-family="Bellota Text, sans-serif" fill="var(--ink)">Step 3</text>
    </svg>
    <p class="step-text" style="top:583px">Slice steak. Serve with onion mixture and rice.</p>
  </section>

  <section class="plate-area">
    <svg class="plate-photo" width="708" height="308" viewBox="0 0 708 308" role="img" aria-label="Photo of sliced five spice beef with choy sum and rice in a white bowl">
      <defs>
        <radialGradient id="food" cx="50%" cy="45%" r="55%">
          <stop offset="0%" stop-color="#8e4d45"/>
          <stop offset="45%" stop-color="#5a4030"/>
          <stop offset="75%" stop-color="#3f5a2e"/>
          <stop offset="100%" stop-color="#d8d4cc"/>
        </radialGradient>
      </defs>
      <circle cx="354" cy="350" r="318" fill="#f2f0ec"/>
      <circle cx="354" cy="370" r="290" fill="#e2dfd9"/>
      <ellipse cx="354" cy="260" rx="230" ry="200" fill="url(#food)"/>
    </svg>
    <div class="pattern-band bottom" role="img" aria-label="Row of soft circle pattern"></div>
  </section>
</main>
</body>
</html>
```